Marta's Dwellings website

We need a simple website for our property investment business in the UK. We basically need our contact details and brief description.We have the company logo already done (via ArtFlockly) so please use these:https://drive.google.com/drive/folders/1szJ3iRhelElZ40NIFT7w-c14MaY3Y_oV?usp=sharingYou could use some stock photos of UK houses for now.Let me know when to provide more detailed descriptions, etc

Coding

Coded - Design and coding required

Number of Pages Required

1 page

Colors

Designer to choose colors to be used in the design.

```html
<!DOCTYPE html>
<html lang="en">
<head>
<meta charset="utf-8">
<title>Marta's Dwellings</title>
<link rel="stylesheet" href="https://fonts.googleapis.com/css2?family=Josefin+Sans:wght@400;600;700&family=Questrial&display=swap">
<style>
:root{
  --blue:#1a66e3;
  --blue-deep:#1250c4;
  --ink:#1b1b1b;
  --text:#4a4a4a;
  --white:#ffffff;
  --footer:#0d0d0d;
  --footer-text:#d6d6d6;
  --map:#e4e6e8;
}
*{margin:0;padding:0;box-sizing:border-box}
html,body{width:1200px;height:3476px;overflow:hidden;background:var(--white)}
body{position:relative;font-family:"Questrial",sans-serif;color:var(--text)}
.abs{position:absolute}
.heading{font-family:"Josefin Sans",sans-serif;font-weight:700;color:var(--ink)}

/* hero */
.hero{left:0;top:0;width:1200px;height:614px;background:linear-gradient(180deg,#2a3547 0%,#4a4a52 25%,#8a5a32 45%,#3b3326 62%,#1e2227 80%,#141719 100%)}
.hero-cut{left:0;top:540px;width:1200px;height:80px}
.brand{left:115px;top:42px;display:flex;align-items:center;gap:12px;color:var(--white);font-family:"Josefin Sans",sans-serif;font-weight:600;font-size:22px;letter-spacing:1px}
.brand .mark{width:14px;height:14px;background:var(--white)}
.phone{right:114px;top:22px;display:flex;align-items:center;gap:10px;color:var(--white);font-family:"Josefin Sans",sans-serif;font-weight:600;font-size:18px}
.nav{right:114px;top:78px;display:flex;gap:37px;font-size:17px;color:var(--white)}
.hero-title{left:0;width:1200px;top:205px;text-align:center;color:var(--white);font-size:60px;text-shadow:0 2px 6px rgba(0,0,0,.5)}
.hero-sub{left:0;width:1200px;top:281px;text-align:center;color:var(--white);font-family:"Josefin Sans",sans-serif;font-weight:600;font-size:16px;line-height:27px;text-shadow:0 1px 4px rgba(0,0,0,.6)}
.btn-outline{left:520px;top:348px;width:162px;height:50px;border:2px solid var(--white);color:var(--white);font-family:"Josefin Sans",sans-serif;font-weight:600;font-size:16px;display:flex;align-items:center;justify-content:center}
.dot{width:12px;height:12px;border-radius:50%;background:var(--white)}
.dot.active{width:28px;height:28px;border:3px solid var(--white);background:none;display:flex;align-items:center;justify-content:center}
.dot.active::after{content:"";width:14px;height:14px;border-radius:50%;background:var(--white)}

/* welcome */
.welcome-pre{left:0;width:1200px;top:666px;text-align:center;font-size:23px;color:#333}
.welcome-title{left:0;width:1200px;top:702px;text-align:center;font-size:50px}
.welcome-text{left:205px;width:790px;top:783px;text-align:center;font-size:15px;line-height:30px;color:#555}
.btn-solid{left:518px;top:954px;width:164px;height:50px;background:var(--blue);color:var(--white);font-family:"Josefin Sans",sans-serif;font-weight:700;font-size:16px;display:flex;align-items:center;justify-content:center}

/* gallery */
.photo{background:linear-gradient(160deg,#7fa4c9 0%,#a0684a 45%,#6f7a4a 100%)}
.photo.alt{background:linear-gradient(170deg,#b9cde0 0%,#b35a3c 50%,#5d7a3d 100%)}
.photo.stone{background:linear-gradient(165deg,#6d8a55 0%,#a89878 50%,#6b6250 100%)}
.tile-active{background:linear-gradient(160deg,#2f72e6,#1d5fd6);display:flex;align-items:center;justify-content:center}

/* news */
.news-title{left:0;width:1200px;top:1780px;text-align:center;font-size:50px}
.card{width:304px}
.card .img{width:304px;height:188px}
.card .meta{display:flex;gap:12px;margin-top:27px;align-items:flex-start}
.date{width:48px;height:48px;border-radius:50%;background:var(--blue);color:var(--white);display:flex;flex-direction:column;align-items:center;justify-content:center;font-family:"Josefin Sans",sans-serif;font-weight:700;font-size:17px;line-height:1;flex:none;margin-top:10px}
.date small{font-size:12px;font-weight:400}
.card h3{font-family:"Josefin Sans",sans-serif;font-weight:600;font-size:18px;line-height:23px;color:var(--ink)}
.card p{margin-top:14px;font-size:15px;line-height:26px;color:#555}
.card .more{margin-top:18px;width:148px;height:42px;border:2px solid var(--ink);display:flex;align-items:center;justify-content:center;font-family:"Josefin Sans",sans-serif;font-weight:600;font-size:15px;color:var(--ink)}

/* quote */
.quote{left:0;top:2401px;width:600px;height:720px;background:linear-gradient(160deg,#2270ea,#1a62de)}
.map{left:600px;top:2401px;width:600px;height:720px;background:linear-gradient(135deg,#e9ebed,#d9dcdf)}
.quote-title{left:112px;top:2500px;font-size:38px;color:var(--white)}
.field{left:112px;width:447px;color:var(--white);font-size:14px;display:flex;align-items:center;gap:10px;border-bottom:2px solid rgba(255,255,255,.85);padding-left:6px}
.submit{left:112px;top:2933px;width:197px;height:61px;border:3px solid var(--white);color:var(--white);font-family:"Josefin Sans",sans-serif;font-weight:700;font-size:22px;display:flex;align-items:center;justify-content:center}
.popup{left:773px;top:2551px;width:358px;height:100px;background:var(--white);box-shadow:0 2px 8px rgba(0,0,0,.2);padding:14px 12px;font-size:14.5px;line-height:25px;color:#222}

/* footer */
.footer{left:0;top:3030px;width:1200px;height:446px}
.footer-head{font-family:"Josefin Sans",sans-serif;font-weight:700;font-size:23px;color:var(--white)}
.footer-text{font-size:14px;line-height:29px;color:var(--footer-text)}
.links{list-style:none;font-size:14.5px;line-height:32px;color:var(--footer-text)}
.contact-row{display:flex;gap:14px;align-items:flex-start;font-size:14px;line-height:26px;color:var(--footer-text)}
.social{width:32px;height:32px;border:2px solid var(--white);border-radius:50%}
.copy{left:109px;top:3428px;font-size:15px;color:var(--footer-text)}
</style>
</head>
<body>

<!-- Hero -->
<div class="abs hero" role="img" aria-label="City skyline at dusk with towers reflected in a river"></div>
<svg class="abs hero-cut" width="1200" height="80" viewBox="0 0 1200 80">
  <polygon points="0,68 600,8 1200,68 1200,74 600,20 0,74" fill="var(--blue)"/>
  <polygon points="0,74 600,20 1200,74 1200,80 0,80" fill="var(--white)"/>
  <polygon points="0,56 600,0 1200,56 1200,68 600,8 0,68" fill="var(--blue)" opacity="0"/>
</svg>
<svg class="abs" style="left:0;top:540px" width="1200" height="80" viewBox="0 0 1200 80">
  <polygon points="0,74 600,12 1200,74 1200,80 0,80" fill="var(--white)"/>
  <polyline points="0,72 600,10 1200,72" fill="none" stroke="var(--blue)" stroke-width="6"/>
</svg>

<div class="abs brand"><span class="mark"></span>Marta's Dwellings</div>
<div class="abs phone">
  <svg width="34" height="34" viewBox="0 0 34 34"><circle cx="17" cy="17" r="15" fill="none" stroke="#fff" stroke-width="2"/><path d="M12 10c1-1 2-1 3 0l1.5 2.5c.5 1 0 1.8-.6 2.4-.6.6-.4 1.2 0 1.8 1 1.6 2 2.6 3.4 3.4.6.4 1.2.6 1.8 0 .6-.6 1.4-1.1 2.4-.6L26 21c1 1 1 2 0 3-2 2-4.5 2-8-.8-3-2.4-5.2-5-6.5-8-1-2.5-.8-4 .5-5.2z" fill="#fff"/></svg>
  (555) 014-2290
</div>
<nav class="abs nav"><span>Home</span><span>About Us</span><span>Our Properties</span><span>Blog</span><span>Contact Us</span></nav>

<h1 class="abs heading hero-title">Marta's Dwellings</h1>
<p class="abs hero-sub">Duis aute irure dolor in reprehenderit in voluptate velit esse<br>cillum dolore eu fugiat nulla pariatur</p>
<div class="abs btn-outline">LEARN MORE</div>
<div class="abs dot active" style="left:1117px;top:265px"></div>
<div class="abs dot" style="left:1125px;top:309px"></div>
<div class="abs dot" style="left:1125px;top:336px"></div>

<!-- Welcome -->
<p class="abs welcome-pre">Welcome To</p>
<h2 class="abs heading welcome-title">Marta's Dwellings</h2>
<p class="abs welcome-text">Nemo enim ipsam voluptatem quia voluptas sit aspernatur aut odit aut fugit, sed quia consequuntur magni dolores eos qui ratione voluptatem sequi nesciunt. Neque porro quisquam est, qui dolorem ipsum quia dolor sit amet, consectetur, adipisci velit, sed quia non numquam eius modi tempora incidunt ut labore et dolore magnam aliquam quaerat voluptatem. Ut enim ad minima veniam, quis nostrum exercitationem ullam corporis suscipit laboriosam, nisi ut aliquid ex ea commodi consequatur</p>
<div class="abs btn-solid">LEARN MORE</div>

<!-- Gallery -->
<div class="abs photo stone" style="left:0;top:1092px;width:596px;height:293px" role="img" aria-label="Stone cottages along a village lane with a small bridge"></div>
<div class="abs photo alt" style="left:605px;top:1092px;width:292px;height:293px" role="img" aria-label="Red brick terraced houses under a grey sky"></div>
<div class="abs photo" style="left:907px;top:1092px;width:293px;height:293px" role="img" aria-label="Couple looking at a large brick house across a lawn"></div>
<div class="abs photo alt" style="left:0;top:1395px;width:290px;height:293px" role="img" aria-label="Detached red brick house on a sunny street"></div>
<div class="abs tile-active" style="left:300px;top:1395px;width:292px;height:293px" role="img" aria-label="Bungalow with conservatory under a blue overlay">
  <svg width="56" height="56" viewBox="0 0 56 56"><circle cx="28" cy="28" r="25" fill="none" stroke="#fff" stroke-width="3"/><path d="M28 16v24M16 28h24" stroke="#fff" stroke-width="3"/></svg>
</div>
<div class="abs photo" style="left:605px;top:1395px;width:595px;height:293px" role="img" aria-label="Row of Victorian red brick houses with gables and trees"></div>

<!-- News -->
<h2 class="abs heading news-title">Latest News</h2>
<article class="abs card" style="left:109px;top:1887px">
  <div class="img photo alt" role="img" aria-label="Red brick townhouses under a blue sky"></div>
  <div class="meta"><div class="date">29<small>Feb</small></div><h3>At vero eos et accusamus et iusto odio dignissimos</h3></div>
  <p>Lorem ipsum dolor sit amet, consectetur adipiscing elit, sed do eiusmod tempor incididunt ut labore et</p>
  <div class="more">READ MORE</div>
</article>
<article class="abs card" style="left:443px;top:1887px">
  <div class="img photo" role="img" aria-label="Brick houses along a suburban road with a hedge"></div>
  <div class="meta"><div class="date">29<small>Feb</small></div><h3>At vero eos et accusamus et iusto odio dignissimos</h3></div>
  <p>Lorem ipsum dolor sit amet, consectetur adipiscing elit, sed do eiusmod tempor incididunt ut labore et</p>
  <div class="more">READ MORE</div>
</article>
<article class="abs card" style="left:780px;top:1887px">
  <div class="img photo stone" role="img" aria-label="Tudor style manor house surrounded by trees"></div>
  <div class="meta"><div class="date">29<small>Feb</small></div><h3>At vero eos et accusamus et iusto odio dignissimos</h3></div>
  <p>Lorem ipsum dolor sit amet, consectetur adipiscing elit, sed do eiusmod tempor incididunt ut labore et</p>
  <div class="more">READ MORE</div>
</article>

<!-- Quote + map -->
<div class="abs quote"></div>
<div class="abs map" role="img" aria-label="Street map around the office location"></div>
<h2 class="abs heading quote-title">Get A Quote</h2>
<div class="abs field" style="top:2585px;height:38px">
  <svg width="12" height="12" viewBox="0 0 12 12"><circle cx="6" cy="3.5" r="3" fill="#fff"/><path d="M0 12c0-4 3-5.5 6-5.5s6 1.5 6 5.5z" fill="#fff"/></svg>Name</div>
<div class="abs field" style="top:2661px;height:32px">
  <svg width="13" height="10" viewBox="0 0 13 10"><rect x=".5" y=".5" width="12" height="9" fill="none" stroke="#fff"/><path d="M.5 .5l6 5 6-5" fill="none" stroke="#fff"/></svg>Email</div>
<div class="abs field" style="top:2737px;height:32px">
  <svg width="12" height="12" viewBox="0 0 12 12"><path d="M2 0l2.5 3-1.5 1.5c.8 1.8 2.2 3.2 4 4L8.5 7 12 9.5 10.5 12C5 12 0 7 0 1.5z" fill="#fff"/></svg>Phone Number</div>
<div class="abs field" style="top:2787px;height:92px;align-items:flex-start">
  <svg width="13" height="10" viewBox="0 0 13 10"><rect width="13" height="10" fill="#fff"/><path d="M0 0l6.5 5L13 0" fill="none" stroke="var(--blue)"/></svg>Message...</div>
<div class="abs submit">Submit</div>

<div class="abs popup">Unit 7, Larkfield Court, 12-14 Orchard Row, Westbridge, Kentshire, United Kingdom, WB4 7QL</div>
<svg class="abs" style="left:890px;top:2662px" width="60" height="78" viewBox="0 0 60 78">
  <path d="M30 78L18 54A28 28 0 1 1 42 54z" fill="#fff"/>
  <circle cx="30" cy="30" r="23" fill="var(--blue)"/>
  <path d="M30 18l-12 11h4v10h6v-6h4v6h6V29h4z" fill="#fff"/>
</svg>

<!-- Footer -->
<svg class="abs footer" width="1200" height="446" viewBox="0 0 1200 446">
  <polygon points="0,75 600,7 1200,75 1200,446 0,446" fill="var(--footer)"/>
  <polyline points="0,72 600,4 1200,72" fill="none" stroke="var(--blue)" stroke-width="6"/>
</svg>

<h3 class="abs footer-head" style="left:112px;top:3143px">About Us</h3>
<p class="abs footer-text" style="left:112px;top:3192px;width:360px">Nemo enim ipsam voluptatem quia voluptas sit aspernatur aut odit aut fugit, sed quia consequuntur magni dolores eos qui ratione voluptatem sequi nesciunt. Neque porro quisquam est, qui dolorem ipsum quia dolor sit</p>

<h3 class="abs footer-head" style="left:548px;top:3143px">Quick Links</h3>
<ul class="abs links" style="left:551px;top:3189px">
  <li>Home</li><li>About Us</li><li>Our Properties</li><li>Blog</li><li>Contact Us</li>
</ul>

<h3 class="abs footer-head" style="left:769px;top:3145px">Contact Us</h3>
<div class="abs contact-row" style="left:771px;top:3194px;width:330px">
  <svg width="16" height="20" viewBox="0 0 16 20" style="flex:none;margin-top:4px"><path d="M8 20S0 11 0 8a8 8 0 0 1 16 0c0 3-8 12-8 12z" fill="#fff"/><circle cx="8" cy="8" r="3" fill="var(--footer)"/></svg>
  <span>Unit 7, Larkfield Court, 12-14 Orchard Row, Westbridge, Kentshire, United Kingdom, WB4 7QL</span>
</div>
<div class="abs contact-row" style="left:771px;top:3286px">
  <svg width="20" height="20" viewBox="0 0 20 20" style="flex:none"><path d="M4 1l4 5-2 2c1.5 3 3 4.5 6 6l2-2 5 4-2.5 3C8 19 1 12 1 3.5z" fill="none" stroke="#fff" stroke-width="1.4"/></svg>
  <span>(555) 014-2290</span>
</div>
<div class="abs contact-row" style="left:771px;top:3334px">
  <svg width="20" height="16" viewBox="0 0 20 16" style="flex:none;margin-top:5px"><rect x=".7" y=".7" width="18.6" height="14.6" fill="none" stroke="#fff" stroke-width="1.4"/><path d="M1 1l9 7 9-7M1 15l6.5-6M19 15l-6.5-6" fill="none" stroke="#fff" stroke-width="1.4"/></svg>
  <span>hello@martasdwellings.example</span>
</div>

<p class="abs copy">© 2019 Company Name &nbsp;|&nbsp; All Rights Reserved</p>
<div class="abs social" style="left:930px;top:3421px"></div>
<div class="abs social" style="left:969px;top:3421px"></div>
<div class="abs social" style="left:1008px;top:3421px"></div>
<div class="abs social" style="left:1047px;top:3421px"></div>

</body>
</html>
```